Coastline Premier Retreats Business Card Design

Design a business card for Coastline Premier Retreats. Look at the website for colors and reference. Card should have logo, name, title, office number, mobile number, email, URL and a tagline like, "Luxury Hotel & Resort Email Marketing" (This might change).

https://www.coastlinepremierretreats.example

The rest I will leave up to your imagination.

Contact Information for Business Card

Logo, name, title, office number, mobile number, email, URL and a tagline like, "Luxury Hotel & Resort Email Marketing" (This might change).

```html
<!DOCTYPE html>
<html lang="en">
<head>
<meta charset="utf-8">
<title>Coastline Premier Retreats – Business Card</title>
<link rel="stylesheet" href="https://fonts.googleapis.com/css2?family=Montserrat:wght@400;500;600;700;800&display=swap">
<style>
  :root {
    --backdrop: #232323;
    --card-dark: #131313;
    --card-light: #ffffff;
    --accent: #f37421;
    --ink: #1c1c1c;
    --paper-text: #ffffff;
  }
  * { box-sizing: border-box; margin: 0; padding: 0; }
  html, body {
    width: 1200px; height: 900px; overflow: hidden;
    background: var(--backdrop);
    font-family: "Montserrat", sans-serif;
  }
  .canvas { position: relative; width: 1200px; height: 900px; }
  .card {
    position: absolute; left: 285px; width: 630px; height: 360px;
    border-radius: 22px; overflow: hidden;
    box-shadow: 0 14px 34px rgba(0,0,0,.45);
  }
  /* Front */
  .card-front { top: 60px; background: var(--card-dark); }
  .front-brand {
    position: absolute; left: 0; right: 0; top: 118px;
    text-align: center; color: var(--paper-text);
    font-weight: 700; font-size: 34px; letter-spacing: .5px;
  }
  .front-rule {
    position: absolute; left: 105px; right: 105px; top: 204px;
    height: 1px; background: var(--accent);
  }
  .front-tagline {
    position: absolute; left: 0; right: 0; top: 226px;
    text-align: center; color: var(--paper-text);
    font-weight: 700; font-size: 13px; letter-spacing: .3px;
  }
  /* Back */
  .card-back { top: 480px; background: var(--card-light); }
  .swoosh { position: absolute; left: 0; top: 0; width: 630px; height: 360px; }
  .back-brand {
    position: absolute; left: 40px; top: 64px;
    display: flex; align-items: center; gap: 10px;
    color: var(--ink); font-weight: 700; font-size: 19px;
  }
  .brand-square { width: 14px; height: 14px; background: var(--accent); }
  .person { position: absolute; right: 46px; top: 44px; text-align: right; }
  .person-name { color: var(--accent); font-weight: 800; font-size: 24px; }
  .person-title { color: var(--ink); font-weight: 400; font-size: 13px; margin-top: 2px; }
  .contact {
    position: absolute; left: 40px; top: 160px;
    color: var(--ink); font-size: 12.5px; line-height: 20px;
  }
  .contact-address { margin-bottom: 4px; }
  .contact-row { display: flex; align-items: center; gap: 9px; }
  .contact-row svg { width: 12px; height: 12px; flex: none; }
  .band-url {
    fill: var(--paper-text); font-family: "Montserrat", sans-serif;
    font-size: 11px; font-weight: 500;
  }
</style>
</head>
<body>
<main class="canvas">
  <section class="card card-front" aria-label="Card front">
    <div class="front-brand">Coastline Premier Retreats</div>
    <div class="front-rule"></div>
    <p class="front-tagline">Luxury Hotel &amp; Resort Email Marketing</p>
  </section>

  <section class="card card-back" aria-label="Card back">
    <svg class="swoosh" viewBox="0 0 630 360">
      <path d="M250 360 C 350 306, 470 262, 630 250 L630 258 C 480 270, 370 312, 290 360 Z" fill="var(--ink)"/>
      <path d="M300 360 C 400 318, 505 284, 630 270 L630 360 Z" fill="var(--accent)"/>
      <defs>
        <path id="band-line" d="M372 350 C 450 322, 530 300, 618 292"/>
      </defs>
      <text class="band-url"><textPath href="#band-line" textLength="240" lengthAdjust="spacing">www.coastlinepremierretreats.example</textPath></text>
    </svg>

    <div class="back-brand"><span class="brand-square"></span>Coastline Premier Retreats</div>

    <div class="person">
      <div class="person-name">Daniel Reyes</div>
      <div class="person-title">Owner</div>
    </div>

    <div class="contact">
      <div class="contact-address">415 Harbor Ave. Suite 210<br>Portland, OR 97201</div>
      <div class="contact-row">
        <svg viewBox="0 0 12 12"><path d="M2 1h2.5l1 3-1.5 1a7 7 0 0 0 3 3l1-1.5 3 1V10a1 1 0 0 1-1 1A9 9 0 0 1 1 2a1 1 0 0 1 1-1z" fill="var(--accent)"/></svg>
        555.210.4470 x 204
      </div>
      <div class="contact-row">
        <svg viewBox="0 0 12 12"><rect x="3" y="0.5" width="6" height="11" rx="1.2" fill="none" stroke="var(--accent)" stroke-width="1.2"/><circle cx="6" cy="9.3" r=".7" fill="var(--accent)"/></svg>
        555.318.2265
      </div>
      <div class="contact-row">
        <svg viewBox="0 0 12 12"><rect x="0.5" y="2" width="11" height="8" fill="var(--accent)"/><path d="M0.5 2 6 6.5 11.5 2" fill="none" stroke="#fff" stroke-width="1"/></svg>
        info@coastlinepremierretreats.example
      </div>
      <div class="contact-row">
        <svg viewBox="0 0 12 12"><circle cx="6" cy="6" r="5.4" fill="var(--accent)"/><path d="M0.8 6h10.4M6 0.6c-2.4 3-2.4 7.8 0 10.8M6 0.6c2.4 3 2.4 7.8 0 10.8" fill="none" stroke="#fff" stroke-width=".8"/></svg>
        www.coastlinepremierretreats.example
      </div>
    </div>
  </section>
</main>
</body>
</html>
```